Borvik Media - Amazing Homepage

We would like to build an amazing homepage for our site. We will need it built in HTM5, so it works across devices and would like it to parallax scroll , so it looks amazing.
We are a digital media agency, that has recently launched. Our old site is self build through one of the standard web build sites. We will be hosting our new site independently.
This is our old site - www.borvik-media.example
The new site only really needs one scrolling page to explain what we do and have our contact details at the bottom.
We have a place to host it, once designed. So we can share with the final design for you to upload.
Attached are:
Brief
Logos and artwork
Our PowerPoint template to give you an idea of colours

```html
<!DOCTYPE html>
<html lang="en">
<head>
<meta charset="utf-8">
<title>Borvik Media – Homepage</title>
<link rel="stylesheet" href="https://fonts.googleapis.com/css2?family=Open+Sans:wght@300;400;600;700;800&display=swap">
<style>
:root{
  --gold:#c59a44;
  --gold-light:#e6c47f;
  --cream:#f7e8c6;
  --ink:#1c1c1c;
  --charcoal:#2a2a2a;
  --text:#4a4a4a;
  --slate:#5a5a5a;
  --mist:#f3f3f3;
  --line:#e2e2e2;
  --white:#ffffff;
}
*{box-sizing:border-box;margin:0;padding:0}
html,body{width:1200px;height:4534px;overflow:hidden}
body{font-family:"Open Sans",Arial,sans-serif;color:var(--text);background:var(--white);position:relative}
section,header,footer{position:absolute;left:0;width:1200px}
.center{text-align:center}
.chevron{position:absolute;left:50%;width:40px;height:22px;margin-left:-20px}
.divider{display:block;margin:14px auto 0;width:160px;height:14px}

/* header */
.site-header{top:0;height:112px;background:var(--white);border-bottom:1px solid var(--line)}
.brand{position:absolute;display:flex;align-items:center;white-space:nowrap}
.brand-dot{display:block;border:2px solid var(--charcoal);border-radius:50%}
.brand-name{font-weight:600;color:var(--charcoal);line-height:1}
.site-header .brand{left:130px;top:36px;gap:12px}
.site-header .brand-dot{width:40px;height:40px}
.site-header .brand-name{font-size:19px}
.main-nav{position:absolute;left:435px;top:48px;display:flex;gap:44px;font-size:14px;font-weight:600;color:var(--charcoal);text-transform:uppercase}
.btn{position:absolute;top:38px;height:42px;line-height:42px;font-size:13px;font-weight:600;color:var(--white);text-align:center;text-transform:uppercase}
.btn-login{left:852px;width:96px;background:var(--charcoal)}
.btn-register{left:966px;width:102px;background:var(--gold)}

/* hero */
.hero{top:112px;height:608px;overflow:hidden}
.hero-visual{position:absolute;inset:0;background:radial-gradient(ellipse at 80% 30%,#4a4a4a 0%,#262626 45%,#121212 100%)}
.hero-copy{position:absolute;top:200px;width:100%;text-align:center;color:var(--white)}
.hero-line{font-size:46px;font-weight:300;letter-spacing:1px;line-height:1.25}
.hero-key{font-size:74px;font-weight:700;color:var(--gold);line-height:1.2;letter-spacing:1px}
.hero-arrow{position:absolute;top:285px;width:28px;height:46px}
.hero-arrow.prev{left:28px}.hero-arrow.next{right:28px}

/* clarity */
.clarity{top:720px;height:640px;background:var(--mist)}
.section-title{font-size:25px;font-weight:700;color:#555;text-transform:uppercase;line-height:1.4}
.clarity .section-title{padding-top:84px}
.pillars{position:absolute;top:185px;left:130px;width:940px;display:flex;justify-content:space-between}
.pillar{width:215px;text-align:center}
.pillar svg{width:150px;height:150px}
.pillar p{font-size:13px;line-height:1.55;color:#6b6b6b;margin-top:18px}
.motto{position:absolute;top:528px;width:100%;text-align:center;color:var(--gold);font-size:19px;font-weight:700;text-transform:uppercase}

/* every client */
.every-client{top:1360px;height:600px;background:var(--white)}
.every-client .section-title{padding-top:92px;font-size:26px}
.case{position:absolute;top:232px;width:448px;height:262px}
.case.left{left:130px}.case.right{left:622px}
.case-visual{position:absolute;inset:0}
.case.left .case-visual{background:linear-gradient(180deg,#0c0c0c 0%,#2b2b2b 55%,#cfcfcf 100%)}
.case.right .case-visual{background:linear-gradient(180deg,#1e1e1e 0%,#3a3a2c 50%,#5e7a2a 100%)}
.case-label{position:absolute;right:0;bottom:0;padding:0 22px;height:60px;line-height:60px;white-space:nowrap;background:rgba(40,40,40,.9);color:var(--white);font-size:16px;font-weight:700;text-align:center;text-transform:uppercase}

/* coup */
.coup{top:1960px;height:602px;background:linear-gradient(180deg,#151515,#262626 70%,#111)}
.coup-copy{position:absolute;top:86px;width:100%;text-align:center;color:var(--white);font-size:24px;font-weight:700;line-height:1.45;text-transform:uppercase}
.coup-copy em{font-style:normal;color:var(--gold)}
.coup-visual{position:absolute;left:430px;top:215px;width:325px;height:365px;background:linear-gradient(180deg,#c49a62 0%,#a9773f 60%,#2a2520 100%)}

/* fight heading */
.fight{top:2562px;height:142px;background:var(--white)}
.fight h2{padding-top:42px;font-size:39px;font-weight:800;color:#555;text-transform:uppercase;text-align:center}
.fight h2 span{color:var(--gold)}

/* growth */
.growth{top:2704px;height:680px;background:var(--gold)}
.growth-lead{position:absolute;top:90px;width:100%;text-align:center;color:var(--cream);font-size:26px;font-weight:400;line-height:1.45;text-transform:uppercase}
.growth-sub{position:absolute;top:216px;width:100%;text-align:center;color:var(--gold-light);font-size:17px;line-height:1.75;text-transform:uppercase}
.services{position:absolute;top:322px;left:110px;width:980px;display:flex;justify-content:space-between}
.service{width:170px;text-align:center}
.service svg{width:100px;height:100px}
.service span{display:block;margin-top:20px;font-size:14px;font-weight:700;color:var(--gold-light);text-transform:uppercase;white-space:nowrap}
.board{position:absolute;top:555px;width:100%;text-align:center;color:var(--gold-light);font-size:17px;font-weight:700;text-transform:uppercase}

/* smash */
.smash{top:3384px;height:428px;background:var(--white)}
.smash p{padding-top:62px;font-size:25px;font-weight:700;color:#555;line-height:1.45;text-transform:uppercase;text-align:center}
.smash .brand{left:0;width:1200px;justify-content:center;top:232px;gap:18px}
.smash .brand-dot{width:80px;height:80px}
.smash .brand-name{font-size:32px}

/* clients */
.clients{top:3812px;height:314px;background:var(--white);border-top:1px solid var(--line)}
.clients .section-title{padding-top:52px;font-size:25px}
.client-row{position:absolute;top:168px;left:130px;width:940px;display:flex;justify-content:space-between;align-items:center}
.client{font-size:24px;font-weight:700;color:var(--slate)}

/* contact */
.contact{top:4126px;height:300px;background:var(--ink)}
.contact h2{padding-top:58px;font-size:25px;font-weight:700;color:var(--white);line-height:1.5;text-transform:uppercase;text-align:center}
.contact h2 span{color:var(--gold)}
.contact .address{position:absolute;top:160px;width:100%;text-align:center;font-size:15px;color:var(--gold)}
.contact .email{position:absolute;top:196px;width:100%;text-align:center;font-size:15px;color:var(--white)}

/* footer */
.site-footer{top:4426px;height:108px;background:var(--gold)}
.footer-nav{position:absolute;left:130px;top:38px;display:flex;gap:18px;font-size:11px;font-weight:600;color:var(--white);text-transform:uppercase}
.copyright{position:absolute;left:130px;top:60px;font-size:10px;color:var(--cream)}
</style>
</head>
<body>

<header class="site-header">
  <div class="brand"><span class="brand-dot"></span><span class="brand-name">Borvik Media</span></div>
  <nav class="main-nav"><span>Home</span><span>What we can offer</span><span>Contact</span></nav>
  <span class="btn btn-login">Login</span>
  <span class="btn btn-register">Register</span>
</header>

<section class="hero">
  <div class="hero-visual" role="img" aria-label="Dark office backdrop with a businesswoman walking and faint digital charts"></div>
  <svg class="hero-arrow prev" viewBox="0 0 28 46"><path d="M24 4 6 23l18 19" fill="none" stroke="#777" stroke-width="6"/></svg>
  <svg class="hero-arrow next" viewBox="0 0 28 46"><path d="M4 4l18 19L4 42" fill="none" stroke="#777" stroke-width="6"/></svg>
  <div class="hero-copy">
    <p class="hero-line">GOT THE FEELING YOUR</p>
    <p class="hero-key">DIGITAL MARKETING</p>
    <p class="hero-line">JUST ISN’T QUITE ‘THERE’?</p>
  </div>
  <svg class="chevron" style="top:548px" viewBox="0 0 40 22"><path d="M4 3l16 15L36 3" fill="none" stroke="#fff" stroke-width="6"/></svg>
</section>

<section class="clarity center">
  <h2 class="section-title">We keep fighting to give you clarity by:</h2>
  <svg class="divider" viewBox="0 0 160 14"><path d="M0 7h70M90 7h70" stroke="#ddd"/><circle cx="80" cy="7" r="4" fill="none" stroke="#ccc"/></svg>
  <div class="pillars">
    <div class="pillar">
      <svg viewBox="0 0 150 150"><circle cx="80" cy="88" r="50" fill="#d6d6d6"/><path d="M56 20a22 22 0 0 1 44 0c0 18-22 44-22 44S56 38 56 20z" fill="var(--gold)"/><circle cx="78" cy="20" r="8" fill="#fff"/></svg>
      <p>Creating a singular view of your digital eco system</p>
    </div>
    <div class="pillar">
      <svg viewBox="0 0 150 150"><path d="M20 20v112h112" fill="none" stroke="#bbb" stroke-width="3"/><rect x="32" y="80" width="14" height="50" fill="#d3d3d3"/><rect x="54" y="60" width="14" height="70" fill="#d3d3d3"/><rect x="76" y="90" width="14" height="40" fill="#d3d3d3"/><circle cx="98" cy="52" r="24" fill="#fff" stroke="var(--gold)" stroke-width="6"/><path d="M115 70l20 22" stroke="var(--gold)" stroke-width="9"/><text x="98" y="62" font-size="28" font-weight="700" fill="var(--gold)" text-anchor="middle" font-family="Open Sans,sans-serif">$</text></svg>
      <p>Reviewing how and why your money is being spent where it is</p>
    </div>
    <div class="pillar">
      <svg viewBox="0 0 150 150"><path d="M96 16h44v28h-30l-10 9v-9h-4z" fill="#fff" stroke="var(--gold)" stroke-width="3"/><circle cx="68" cy="62" r="12" fill="#c8c8c8"/><path d="M50 98a18 18 0 0 1 36 0z" fill="#c8c8c8"/><circle cx="40" cy="92" r="11" fill="#c8c8c8"/><path d="M22 128a18 18 0 0 1 36 0z" fill="#c8c8c8"/><circle cx="96" cy="92" r="11" fill="#c8c8c8"/><path d="M78 128a18 18 0 0 1 36 0z" fill="#c8c8c8"/></svg>
      <p>Profiling your customers. Who doesn’t have 1000’s of different customer with different motivations, interests and value to the brand?</p>
    </div>
    <div class="pillar">
      <svg viewBox="0 0 150 150"><rect x="38" y="14" width="66" height="90" rx="4" fill="#d8d8d8"/><circle cx="82" cy="82" r="28" fill="#fff" stroke="var(--gold)" stroke-width="8"/><path d="M102 102l26 26" stroke="var(--gold)" stroke-width="12" stroke-linecap="round"/></svg>
      <p>Finding the best digital channels to communicate with them. Because everything is changing every day... exciting isn’t it!</p>
    </div>
  </div>
  <p class="motto">Never stop, never settle, always improve. Be amazing.</p>
  <svg class="chevron" style="top:590px" viewBox="0 0 40 22"><path d="M4 3l16 15L36 3" fill="none" stroke="#ccc" stroke-width="6"/></svg>
</section>

<section class="every-client center">
  <h2 class="section-title">Every client deserves amazing work,<br>regardless of the brand, it’s all real money</h2>
  <svg class="divider" viewBox="0 0 160 14"><path d="M0 7h70M90 7h70" stroke="#ddd"/><circle cx="80" cy="7" r="4" fill="none" stroke="#ccc"/></svg>
  <div class="case left"><div class="case-visual" role="img" aria-label="Glossy marbles on a chequered floor"></div><span class="case-label">Marbles</span></div>
  <div class="case right"><div class="case-visual" role="img" aria-label="Football resting on grass"></div><span class="case-label">Football stickers</span></div>
  <svg class="chevron" style="top:548px" viewBox="0 0 40 22"><path d="M4 3l16 15L36 3" fill="none" stroke="#ddd" stroke-width="6"/></svg>
</section>

<section class="coup">
  <p class="coup-copy">It’s time to start a coup…there are too many large<br>agency networks, <em>too few agencies being transparent</em>, too<br>many putting quality of work second to income</p>
  <div class="coup-visual" role="img" aria-label="Wooden soap box crate standing on a reflective dark floor"></div>
</section>

<section class="fight">
  <h2>We keep fighting to give <span>you clarity by:</span></h2>
</section>

<section class="growth">
  <p class="growth-lead">We’ve yet to come across a client that wants to shrink…<br>making us specialists in delivering growth!</p>
  <p class="growth-sub">We’ve been optimising our digital knowledge for over 20 years and<br>we genuinely know what we are talking about...</p>
  <div class="services">
    <div class="service"><svg viewBox="0 0 100 100" fill="none" stroke="#e0b870" stroke-width="6"><path d="M50 50v44M38 94h24"/><circle cx="50" cy="42" r="7" fill="#e0b870"/><path d="M34 26a22 22 0 0 0 0 32M66 26a22 22 0 0 1 0 32M22 14a38 38 0 0 0 0 56M78 14a38 38 0 0 1 0 56"/></svg><span>PPC</span></div>
    <div class="service"><svg viewBox="0 0 100 100" fill="#e0b870"><rect x="8" y="70" width="14" height="26"/><rect x="28" y="58" width="14" height="38"/><rect x="48" y="44" width="14" height="52"/><rect x="68" y="30" width="14" height="66"/><path d="M10 52 70 12" stroke="#e0b870" stroke-width="6"/><path d="M60 6h22v22z"/></svg><span>SEO</span></div>
    <div class="service"><svg viewBox="0 0 100 100" fill="#e0b870"><rect x="8" y="8" width="24" height="24"/><rect x="38" y="8" width="24" height="24"/><rect x="68" y="8" width="24" height="24"/><rect x="8" y="38" width="24" height="24"/><rect x="38" y="38" width="24" height="24"/><rect x="68" y="38" width="24" height="24"/><rect x="8" y="68" width="24" height="24"/><rect x="38" y="68" width="24" height="24"/><rect x="68" y="68" width="24" height="24"/></svg><span>Display</span></div>
    <div class="service"><svg viewBox="0 0 100 100" fill="none" stroke="#e0b870" stroke-width="6" stroke-linejoin="round"><path d="M4 40l20-14 18 6 14-8 20 4 20 14M24 26l-10 30 30 24 8-6M76 28l12 28-24 22"/><path d="M42 60l10 8M50 52l12 10M58 46l12 10"/></svg><span>Paid social</span></div>
    <div class="service"><svg viewBox="0 0 100 100" fill="#e0b870"><ellipse cx="64" cy="22" rx="28" ry="10"/><rect x="36" y="22" width="56" height="56"/><ellipse cx="64" cy="78" rx="28" ry="10"/><path d="M36 44a28 10 0 0 0 56 0M36 62a28 10 0 0 0 56 0" stroke="var(--gold)" stroke-width="3" fill="none"/><rect x="6" y="54" width="24" height="36"/></svg><span>Data management</span></div>
    <div class="service"><svg viewBox="0 0 100 100" fill="#e0b870"><rect x="34" y="4" width="20" height="58"/><path d="M20 60h48L44 92z"/><rect x="62" y="30" width="30" height="8"/><rect x="62" y="48" width="30" height="8"/><rect x="62" y="84" width="30" height="8"/></svg><span>Attribution</span></div>
  </div>
  <p class="board">Operating at board level in top 10 digital agencies</p>
  <svg class="chevron" style="top:618px" viewBox="0 0 40 22"><path d="M4 3l16 15L36 3" fill="none" stroke="#e6c47f" stroke-width="6"/></svg>
</section>

<section class="smash">
  <p>Happily, we smash it for all our clients, with an average<br>of 35% improvement in performance within the first quarter<br>of working with us</p>
  <div class="brand"><span class="brand-dot"></span><span class="brand-name">Borvik Media</span></div>
  <svg class="chevron" style="top:380px" viewBox="0 0 40 22"><path d="M4 3l16 15L36 3" fill="none" stroke="#ddd" stroke-width="6"/></svg>
</section>

<section class="clients center">
  <h2 class="section-title">Logos of clients</h2>
  <svg class="divider" viewBox="0 0 160 14"><path d="M0 7h70M90 7h70" stroke="#ddd"/><circle cx="80" cy="7" r="4" fill="none" stroke="#ccc"/></svg>
  <div class="client-row">
    <span class="client">Kestrel DIY</span>
    <span class="client">Mendora</span>
    <span class="client">Lumeo</span>
    <span class="client">Ambrose Lane</span>
    <span class="client">Nightjar</span>
  </div>
</section>

<section class="contact">
  <h2>If you are still reading our rant then get in touch /<br>follow us / <span>let’s go for a coffee</span></h2>
  <p class="address">Our address is 14 Larkspur Row, London, E2 7QD</p>
  <p class="email">contact@borvik-media.example</p>
</section>

<footer class="site-footer">
  <nav class="footer-nav"><span>Home</span><span>What we can offer</span><span>Contact</span></nav>
  <p class="copyright">Copyright © 2014 borvik-media.example. All Rights Reserved.</p>
</footer>

</body>
</html>
```